Emergency and Referral Vet Hospital promotional sticker design

We're looking at getting some stickers designed that we could give to clients to put on their cars for promotion and advertising. If they could also be suitable for a goodie bag for conference too that would be great. I like the look of water-colour backgrounds, we'll need to include our logo and probably our address (Unit 3/215 Korrinup Road Tallowmere). We also have a hospital motto "... because they're family" if that could somehow be integrated, we only care for small animals (dogs, cats etc) but the design is very open to suggestion. Would love to see what you can create.

Industry/Entity Type

Veterinary

Colors
0054AA
0677BA
7BADD7
CADEEF
E8F1F8
0094D4
00A9DD
6FCCEA
C7EBF8
E9F6FB

Requirements
Nice to have
• Think beach vibes, blues maybe paw print shapes etc

```html
<!DOCTYPE html>
<html lang="en">
<head>
<meta charset="utf-8">
<title>tidepool – sticker design</title>
<link href="https://fonts.googleapis.com/css2?family=Kaushan+Script&family=Quicksand:wght@500;700&display=swap" rel="stylesheet">
<style>
  :root {
    --page: #ffffff;
    --ink: #111111;
    --night: #000000;
    --motto: #ffffff;
    --paw: #ffffff;
    --cross-line: rgba(255,255,255,0.85);
    --sand-1: #f6ece6;
    --sand-2: #ecdcd2;
    --orchid-1: #e4c6f2;
    --orchid-2: #c691de;
    --violet-1: #b689ea;
    --violet-2: #9564dc;
    --lavender-1: #dcd7f7;
    --lavender-2: #a49cea;
    --brand-dot: #2f8f9c;
  }
  html, body {
    margin: 0;
    padding: 0;
    width: 1000px;
    height: 1200px;
    overflow: hidden;
    background: var(--page);
  }
  .canvas {
    display: block;
    width: 1000px;
    height: 1200px;
  }
  .motto {
    font-family: "Kaushan Script", cursive;
    font-size: 54px;
    fill: var(--motto);
  }
  .brand-name {
    font-family: "Quicksand", sans-serif;
    font-weight: 700;
    font-size: 36px;
    fill: var(--ink);
  }
  .address {
    font-family: "Quicksand", sans-serif;
    font-weight: 700;
    font-size: 15px;
    fill: var(--ink);
  }
  .paw { fill: var(--paw); }
  .cross-outline {
    fill: none;
    stroke: var(--cross-line);
    stroke-width: 1.2;
  }
  .night-corner { fill: var(--night); }
  .sticker-cut {
    stroke: #ffffff;
    stroke-width: 22;
    stroke-linejoin: round;
  }
</style>
</head>
<body>
<svg class="canvas" viewBox="0 0 1000 1200" xmlns="http://www.w3.org/2000/svg">
  <defs>
    <linearGradient id="sand" x1="0" y1="0" x2="1" y2="1">
      <stop offset="0" stop-color="var(--sand-1)"/>
      <stop offset="1" stop-color="var(--sand-2)"/>
    </linearGradient>
    <linearGradient id="orchid" x1="0.6" y1="0" x2="0.3" y2="1">
      <stop offset="0" stop-color="var(--orchid-2)"/>
      <stop offset="1" stop-color="var(--orchid-1)"/>
    </linearGradient>
    <linearGradient id="violet" x1="0" y1="0" x2="1" y2="1">
      <stop offset="0" stop-color="var(--violet-1)"/>
      <stop offset="1" stop-color="var(--violet-2)"/>
    </linearGradient>
    <linearGradient id="lavender" x1="0.3" y1="0" x2="0.5" y2="1">
      <stop offset="0" stop-color="var(--lavender-1)"/>
      <stop offset="1" stop-color="var(--lavender-2)"/>
    </linearGradient>

    <symbol id="paw-print" viewBox="0 0 100 100">
      <ellipse cx="50" cy="68" rx="27" ry="22"/>
      <ellipse cx="20" cy="40" rx="10" ry="13" transform="rotate(-20 20 40)"/>
      <ellipse cx="38" cy="22" rx="10" ry="14" transform="rotate(-8 38 22)"/>
      <ellipse cx="62" cy="22" rx="10" ry="14" transform="rotate(8 62 22)"/>
      <ellipse cx="80" cy="40" rx="10" ry="13" transform="rotate(20 80 40)"/>
    </symbol>

    <g id="watercolour-wash" role="img" aria-label="Soft watercolour washes in sand, orchid, violet and lavender with gold flecks">
      <path fill="url(#sand)" d="M170 180 C200 90 330 60 420 75 C500 90 545 160 535 250 C530 330 520 420 470 470 C420 520 300 530 230 500 C170 470 150 380 155 300 C155 250 160 210 170 180 Z"/>
      <path fill="url(#lavender)" d="M560 200 C620 170 730 185 790 230 C850 280 870 370 850 440 C870 510 840 600 760 625 C680 645 600 625 570 570 C540 510 590 470 580 410 C560 340 520 260 560 200 Z"/>
      <path fill="url(#orchid)" d="M330 215 C380 190 470 195 520 230 C580 270 600 360 580 430 C575 520 560 600 480 640 C400 660 280 655 220 630 C190 600 200 520 250 480 C290 440 280 380 300 320 C310 270 300 235 330 215 Z"/>
      <path fill="url(#violet)" d="M470 215 C540 190 640 230 670 290 C690 350 660 430 600 470 C560 500 490 490 470 440 C450 380 440 260 470 215 Z"/>
    </g>

    <g id="sticker-design">
      <use href="#watercolour-wash"/>
      <use href="#paw-print" class="paw" x="458" y="200" width="115" height="115"/>
      <text class="motto" x="230" y="378">… because they’re family</text>
      <rect class="cross-outline" x="642" y="387" width="110" height="200" rx="10"/>
      <rect class="cross-outline" x="597" y="432" width="200" height="110" rx="10"/>
      <path fill="var(--lavender-2)" d="M643 433 h108 v108 h-108 Z" opacity="0"/>
      <use href="#paw-print" class="paw" x="668" y="458" width="60" height="60"/>
      <circle cx="248" cy="494" r="14" fill="var(--brand-dot)"/>
      <text class="brand-name" x="225" y="540">tidepool</text>
      <text class="address" x="225" y="565">Unit 3</text>
      <text class="address" x="225" y="587">215 Korrinup Road Tallowmere</text>
    </g>
  </defs>

  <polygon class="night-corner" points="0,1112 1000,705 1000,1200 0,1200"/>

  <g class="design-flat">
    <use href="#sticker-design"/>
  </g>

  <g class="design-sticker" transform="translate(297 621) scale(0.716)">
    <use href="#watercolour-wash" class="sticker-cut"/>
    <use href="#sticker-design"/>
  </g>
</svg>
</body>
</html>
```